Business Card for a Jewellery Brand

Business card for an upscale jewellery brand. Attached is the brand logo and icon and color board. I am looking for two card versions: one for the founder and one is generic. The card should be elegant and convey upscale and premium feel. I am open to both square and rectangle card shapes.

Industry/Entity Type

Jewelry

Contact Information for Business Card

Two cards: (1) Sunela Parvaniya (Founder) (2) General
(1) Sunela Parvaniya card should have Name: Sunela Parvaniya, Title: Founder Email id: sunela@quiremo.com.au. Phone no: +61452913307
(2) Generic card should have Email id: info@quiremo.com.au. Phone no: +61436207518

Requirements
Must have
• Workmark
• ICON
• Phone no
• Email ID
• ABN: 58219740312 (Note: ABN is Business number in Australia)
• Website: www.quiremo.com.au
• Instagram: quiremo_jewellery
• Facebook: @quiremojewellery
Nice to have
• Tagline

```html
<!DOCTYPE html>
<html lang="en">
<head>
<meta charset="utf-8">
<title>Quiremo Business Cards</title>
<link rel="stylesheet" href="https://fonts.googleapis.com/css2?family=Montserrat:wght@500;600;700&family=Open+Sans:wght@400;600&display=swap">
<style>
  :root {
    --backdrop: #a9a9a9;
    --card-black: #0b0b0b;
    --card-vein: #1c1c1c;
    --copper: #e08a55;
    --copper-deep: #c8743f;
    --soft-grey: #c9c9c9;
    --rule-grey: #8f8f8f;
    --icon-grey: #8a8a8a;
  }
  * { margin: 0; padding: 0; box-sizing: border-box; }
  html, body {
    width: 1200px; height: 900px; overflow: hidden;
    background: var(--backdrop);
  }
  .stage { position: relative; width: 1200px; height: 900px; }

  .card {
    position: absolute; top: 238px;
    width: 400px; height: 400px;
    background: var(--card-black);
    overflow: hidden;
  }
  .card--founder { left: 192px; }
  .card--general { left: 636px; }

  .card__surface {
    position: absolute; inset: 0;
    background: linear-gradient(135deg, var(--card-black) 0%, var(--card-vein) 45%, var(--card-black) 55%, #141414 100%);
  }
  .card__content { position: absolute; inset: 0; }

  .person__name {
    position: absolute; left: 26px; top: 38px;
    font: 700 21px/1 "Montserrat", sans-serif;
    color: var(--copper); letter-spacing: 0.2px;
  }
  .person__title {
    position: absolute; left: 26px; top: 69px;
    font: 400 17px/1 "Open Sans", sans-serif;
    color: var(--soft-grey);
  }

  .wordmark {
    position: absolute; left: 0; right: 0;
    text-align: center;
    font: 500 58px/1 "Montserrat", sans-serif;
    color: var(--copper);
    letter-spacing: 10px;
    padding-left: 10px;
  }
  .card--founder .wordmark { top: 153px; }
  .card--general .wordmark { top: 170px; font-size: 46px; letter-spacing: 9px; }

  .contact-list {
    position: absolute; left: 26px; top: 274px;
    list-style: none;
  }
  .contact-list li {
    display: flex; align-items: center; gap: 7px;
    height: 23.5px;
    font: 400 16px/1 "Open Sans", sans-serif;
    color: var(--soft-grey);
  }
  .contact-list svg { width: 12px; height: 12px; fill: var(--copper); flex: none; }

  .abn {
    position: absolute; left: 24px; top: 361px;
    font: 400 16px/1 "Open Sans", sans-serif;
    color: var(--soft-grey);
  }
  .abn__label { font-weight: 600; color: var(--copper); }

  .social {
    position: absolute; left: 39px; top: 263px;
    width: 322px; height: 26px;
    display: flex; align-items: center; gap: 11px;
  }
  .social__rule { flex: 1; height: 1px; background: var(--rule-grey); }
  .social__dot {
    width: 24px; height: 24px; border-radius: 50%;
    background: var(--icon-grey); flex: none;
  }
  .social__dot + .social__dot { margin-left: -1px; }
  .social__handle {
    position: absolute; left: 0; right: 0; top: 301px;
    text-align: center;
    font: 400 16px/1 "Open Sans", sans-serif;
    color: var(--copper);
  }
</style>
</head>
<body>
<main class="stage">

  <section class="card card--founder">
    <div class="card__surface" role="img" aria-label="Black marble texture with white veins"></div>
    <div class="card__content">
      <h1 class="person__name">SUNELA PARVANIYA</h1>
      <p class="person__title">Founder</p>

      <p class="wordmark">QUIREMO</p>

      <ul class="contact-list">
        <li>
          <svg viewBox="0 0 24 24" aria-hidden="true"><path d="M6.6 10.8a15.1 15.1 0 0 0 6.6 6.6l2.2-2.2c.3-.3.7-.4 1-.2 1.1.4 2.3.6 3.6.6.6 0 1 .4 1 1V20c0 .6-.4 1-1 1C10.6 21 3 13.4 3 4c0-.6.4-1 1-1h3.5c.6 0 1 .4 1 1 0 1.3.2 2.5.6 3.6.1.3 0 .7-.2 1z"/></svg>
          +61452913307
        </li>
        <li>
          <svg viewBox="0 0 24 24" aria-hidden="true"><path d="M2 5h20v14H2z M2 5l10 8 10-8" /><path d="M3 6.5l9 7 9-7V18H3z" fill="#0b0b0b" opacity="0"/></svg>
          sunela@quiremo.com.au.
        </li>
        <li>
          <svg viewBox="0 0 24 24" aria-hidden="true"><circle cx="12" cy="12" r="10"/><path d="M7 9l3-2 2 3-2 3 3 3-1 4-3-4-2-4zM15 6l3 2-1 3-3-1z" fill="#0b0b0b"/></svg>
          www.quiremo.com.au
        </li>
      </ul>

      <p class="abn"><span class="abn__label">ABN:</span> 58219740312</p>
    </div>
  </section>

  <section class="card card--general">
    <div class="card__surface" role="img" aria-label="Black marble texture with white veins"></div>
    <div class="card__content">
      <p class="wordmark">QUIREMO</p>

      <div class="social">
        <span class="social__rule"></span>
        <span class="social__dot" aria-hidden="true"></span>
        <span class="social__dot" aria-hidden="true"></span>
        <span class="social__rule"></span>
      </div>
      <p class="social__handle">@quiremojewellery</p>
    </div>
  </section>

</main>
</body>
</html>
```